Corporate Business Card

Very professional, Modern, Not to busy, include phone address email, website
(253) 617-4930, 18761 52nd Avenue S, Kent, WA 98047, martin@plumlinegroup.com, varkoworks.com

Target Market(s)

Manufacturing

Industry/Entity Type

Aero, machining, manufacturing, Off road racing

Contact Information for Business Card

Phone, address email, website

```html
<!DOCTYPE html>
<html lang="en">
<head>
<meta charset="utf-8">
<title>Varko Works – Business Card</title>
<link href="https://fonts.googleapis.com/css2?family=Montserrat:wght@500;600;700&display=swap" rel="stylesheet">
<style>
  :root {
    --bg: #d0d0d0;
    --paper: #f7f7f7;
    --navy: #4a5f96;
    --brand-blue: #1f3a78;
    --red: #e0404a;
    --ink: #2b2b2b;
    --white: #ffffff;
  }
  * { margin: 0; padding: 0; box-sizing: border-box; }
  html, body { width: 1200px; height: 900px; overflow: hidden; }
  body {
    background: var(--bg);
    font-family: "Montserrat", Arial, sans-serif;
    position: relative;
  }
  .showcase-wordmark {
    position: absolute;
    top: 60px;
    right: 70px;
    font-weight: 700;
    font-size: 30px;
    letter-spacing: 2px;
    color: var(--brand-blue);
  }
  .card {
    position: absolute;
    top: 330px;
    width: 500px;
    height: 286px;
    overflow: hidden;
    box-shadow: 0 10px 24px rgba(0,0,0,0.18);
  }
  .card--front { left: 70px; background: var(--paper); }
  .card--back { left: 630px; background: var(--navy); }

  .card__band {
    position: absolute;
    left: 0; right: 0; bottom: 0;
    height: 24px;
    display: flex;
  }
  .card__band-accent { width: 64px; background: var(--red); }
  .card__band-fill { flex: 1; }
  .card--front .card__band-fill { background: var(--navy); }
  .card--back .card__band-fill { background: var(--white); }

  .card__brand {
    position: absolute;
    top: 34px;
    right: 36px;
    font-weight: 700;
    font-size: 17px;
    letter-spacing: 1.5px;
    color: var(--brand-blue);
  }
  .holder { position: absolute; left: 40px; top: 120px; }
  .holder__name {
    font-weight: 700;
    font-size: 25px;
    color: var(--navy);
    line-height: 1;
  }
  .holder__position {
    margin-top: 5px;
    font-weight: 600;
    font-size: 9px;
    letter-spacing: 2.5px;
    color: var(--red);
  }
  .contact {
    list-style: none;
    margin-top: 16px;
    margin-left: 20px;
  }
  .contact__item {
    display: flex;
    align-items: center;
    gap: 8px;
    font-size: 10.5px;
    font-weight: 500;
    color: var(--ink);
    line-height: 19px;
  }
  .contact__icon { width: 10px; height: 10px; fill: var(--ink); flex: none; }

  .card__brand--center {
    top: 50%;
    left: 50%;
    right: auto;
    transform: translate(-50%, -60%);
    font-size: 40px;
    letter-spacing: 3px;
    color: var(--white);
    white-space: nowrap;
  }
</style>
</head>
<body>
  <div class="showcase-wordmark">VARKO WORKS</div>

  <section class="card card--front">
    <div class="card__brand">VARKO WORKS</div>
    <div class="holder">
      <div class="holder__name">Your Name</div>
      <div class="holder__position">POSITION</div>
      <ul class="contact">
        <li class="contact__item">
          <svg class="contact__icon" viewBox="0 0 10 10"><path d="M2 0.5 L3.6 2.6 L2.8 3.6 Q3.8 5.8 6.4 7.2 L7.4 6.4 L9.5 8 L8.4 9.5 Q1.5 8 0.5 1.6 Z"/></svg>
          (253) 617-4930
        </li>
        <li class="contact__item">
          <svg class="contact__icon" viewBox="0 0 10 10"><path d="M5 0.3 A3.4 3.4 0 0 1 8.4 3.7 C8.4 6 5 9.7 5 9.7 C5 9.7 1.6 6 1.6 3.7 A3.4 3.4 0 0 1 5 0.3 Z M5 2.4 A1.3 1.3 0 1 0 5 5 A1.3 1.3 0 1 0 5 2.4 Z" fill-rule="evenodd"/></svg>
          18761 52nd Avenue S, Kent, WA 98047
        </li>
        <li class="contact__item">
          <svg class="contact__icon" viewBox="0 0 10 10"><circle cx="5" cy="5" r="4.3" fill="none" stroke="#2b2b2b" stroke-width="1"/><ellipse cx="5" cy="5" rx="1.8" ry="4.3" fill="none" stroke="#2b2b2b" stroke-width="0.9"/><path d="M0.7 5 H9.3" stroke="#2b2b2b" stroke-width="0.9"/></svg>
          varkoworks.com
        </li>
        <li class="contact__item">
          <svg class="contact__icon" viewBox="0 0 10 10"><path d="M0.5 2 H9.5 V8.2 H0.5 Z M1 2.4 L5 5.6 L9 2.4" fill="none" stroke="#2b2b2b" stroke-width="1"/></svg>
          martin@plumlinegroup.com
        </li>
      </ul>
    </div>
    <div class="card__band"><div class="card__band-accent"></div><div class="card__band-fill"></div></div>
  </section>

  <section class="card card--back">
    <div class="card__brand card__brand--center">VARKO WORKS</div>
    <div class="card__band"><div class="card__band-accent"></div><div class="card__band-fill"></div></div>
  </section>
</body>
</html>
```